Book Cover for Productivity Book

I need a book cover for my latest publication "On Momentum: The Gathered Insights of the Swiftest Worker Breathing"

You can see my branding at www.quillmarrow.com

This is meant to be my epic pinaccle work on productivity, I want it to look like the end all be all word on productivity.

Target Market(s)

entrepreneurs

```html
<!DOCTYPE html>
<html lang="en">
<head>
<meta charset="utf-8">
<title>On Momentum — Book Cover</title>
<link rel="stylesheet" href="https://fonts.googleapis.com/css2?family=Bebas+Neue&family=Montserrat:wght@700&display=swap">
<style>
  :root {
    --backdrop: #cbcbcd;
    --paper: #dedede;
    --oxblood: #58000c;
  }
  html, body {
    margin: 0;
    padding: 0;
    width: 1200px;
    height: 1200px;
    overflow: hidden;
    background: var(--backdrop);
  }
  .stage {
    position: relative;
    width: 1200px;
    height: 1200px;
  }
  .book-cover {
    position: absolute;
    left: 230px;
    top: 50px;
    width: 740px;
    height: 1100px;
    display: block;
  }
  .cover-paper { fill: var(--paper); }
  .cover-band { fill: var(--oxblood); }
  .title {
    font-family: "Bebas Neue", "Oswald", sans-serif;
    font-size: 160px;
    letter-spacing: 1px;
  }
  .subtitle {
    font-family: "Montserrat", sans-serif;
    font-weight: 700;
    font-size: 41px;
  }
  .ink-dark { fill: var(--oxblood); }
  .ink-light { fill: var(--paper); }
</style>
</head>
<body>
<main class="stage">
  <svg class="book-cover" viewBox="0 0 740 1100" xmlns="http://www.w3.org/2000/svg" role="img" aria-label="On Momentum: The Gathered Insights of the Swiftest Worker Breathing">
    <defs>
      <clipPath id="paper-side"><rect x="0" y="0" width="374" height="1100"/></clipPath>
      <clipPath id="band-side"><rect x="374" y="0" width="366" height="1100"/></clipPath>
      <g id="cover-type">
        <text class="title" x="306" y="225">ON</text>
        <text class="title" x="72" y="361" textLength="570" lengthAdjust="spacingAndGlyphs">MOMENTUM</text>
        <text class="subtitle" transform="translate(348 1035) rotate(-90)" textLength="615" lengthAdjust="spacingAndGlyphs">The Gathered Insights of the</text>
        <text class="subtitle" transform="translate(414 1035) rotate(-90)">Swiftest Worker Breathing</text>
      </g>
    </defs>

    <rect class="cover-paper" x="0" y="0" width="740" height="1100"/>
    <rect class="cover-band" x="374" y="0" width="366" height="1100"/>

    <g class="ink-dark" clip-path="url(#paper-side)"><use href="#cover-type"/></g>
    <g class="ink-light" clip-path="url(#band-side)"><use href="#cover-type"/></g>
  </svg>
</main>
</body>
</html>
```